Business Card for Vorla Parts Wholesale supplier

Hi There! I need a new business card for our company. We are specialized in selling Vorla parts, mostly we sell new LCD screens for Zelnar and Drelks. I would like to see that back in the design.

You can find the colors and logo's on our website: www.hartuvo.nl

Industry/Entity Type

Business

Contact Information for Business Card

My Details:
Tobias Lindqvist

Phone: 0031687203316
E-mail: Tobias@hartuvo.nl

Slogan: "Because Quality Matters"

Font styles to use
Sans Serif

Colors

Designer to choose colors to be used in the design.

Requirements
Must have
• A Black backside with the Hartuvo logo on it. The front side should be clean with only my contact details.
• But I'm also open for something really different or awesome!
Nice to have
• Remember that we are in the parts & repairing industry, So i'll be handing those business cards mainly to repair companies. Maybe you can do something with that thought :)

```html
<!DOCTYPE html>
<html lang="en">
<head>
<meta charset="utf-8">
<title>Hartuvo Business Card</title>
<link rel="stylesheet" href="https://fonts.googleapis.com/css2?family=Open+Sans:wght@400;600;700&display=swap">
<style>
  :root {
    --backdrop-top: #bdbdbd;
    --backdrop-bottom: #a9a9a9;
    --brand-orange: #f37327;
    --card-white: #ffffff;
    --card-dark: #3b3b3b;
    --ink: #1a1a1a;
    --light-ink: #ffffff;
    --device-tint-a: #f4f4f4;
    --device-tint-b: #e6e6e6;
  }
  * { margin: 0; padding: 0; box-sizing: border-box; }
  html, body {
    width: 1200px; height: 900px; overflow: hidden;
    font-family: "Open Sans", Arial, sans-serif;
  }
  .stage {
    position: relative; width: 1200px; height: 900px;
    background: linear-gradient(180deg, var(--backdrop-top), var(--backdrop-bottom));
  }
  .card {
    position: absolute; top: 170px; width: 347px; height: 561px; overflow: hidden;
  }
  .card--front { left: 259px; background: var(--card-white); }
  .card--back { left: 631px; background: var(--card-dark); }

  /* front */
  .front-brand {
    position: absolute; top: 272px; left: 0; width: 100%;
    display: flex; align-items: center; justify-content: center; gap: 12px;
    color: var(--brand-orange); font-weight: 700; font-size: 40px; letter-spacing: 0.5px;
    top: 60px; height: 170px;
  }
  .front-brand__square { width: 34px; height: 34px; background: var(--brand-orange); }
  .device-visual {
    position: absolute; left: 9px; top: 235px; width: 330px; height: 326px;
    background: linear-gradient(180deg, var(--device-tint-b) 0%, var(--device-tint-a) 60%, var(--card-white) 100%);
    opacity: 0.75;
  }
  .holder-name {
    position: absolute; top: 334px; width: 100%; text-align: center;
    color: var(--brand-orange); font-size: 20px; font-weight: 600; letter-spacing: 0.5px;
  }
  .contact-icons {
    position: absolute; top: 393px; width: 100%;
    display: flex; justify-content: center; gap: 5px;
  }
  .contact-icons svg { width: 13px; height: 13px; fill: var(--brand-orange); }
  .contact-list {
    position: absolute; top: 425px; width: 100%; list-style: none; text-align: center;
    color: var(--ink); font-size: 15px; line-height: 20px;
  }
  .slogan {
    position: absolute; top: 510px; width: 100%; text-align: center;
    color: var(--brand-orange); font-size: 16px; font-weight: 600;
  }

  /* back */
  .back-square {
    position: absolute; left: 146px; top: 150px; width: 56px; height: 56px;
    background: var(--brand-orange);
  }
  .back-wordmark {
    position: absolute; top: 236px; width: 100%; text-align: center;
    color: var(--light-ink); font-size: 70px; font-weight: 600; letter-spacing: 1px; line-height: 1;
  }
  .back-tagline {
    position: absolute; top: 350px; width: 100%; text-align: center;
    color: var(--light-ink); font-size: 28px; font-weight: 600; line-height: 41px;
  }
</style>
</head>
<body>
<main class="stage">
  <section class="card card--front" aria-label="Card front">
    <div class="device-visual" role="img" aria-label="Faint image of a smartphone LCD screen replacement part"></div>
    <div class="front-brand"><span class="front-brand__square"></span>Hartuvo</div>
    <h1 class="holder-name">TOBIAS LINDQVIST</h1>
    <div class="contact-icons" aria-hidden="true">
      <svg viewBox="0 0 16 16"><path d="M3.6 1.2l2.3 2.8-1.3 1.8c.9 2 2.6 3.7 4.6 4.6l1.8-1.3 2.8 2.3-1.3 2.4C7.6 13.6 2.4 8.4 1.2 3.4z"/></svg>
      <svg viewBox="0 0 16 16"><path d="M1 3h14v10H1z M2 4l6 5 6-5" fill="var(--brand-orange)"/><path d="M2.2 4.2L8 8.8l5.8-4.6" stroke="#fff" stroke-width="1.2" fill="none"/></svg>
      <svg viewBox="0 0 16 16"><circle cx="8" cy="8" r="7"/><path d="M5 4c2 1 1 3 3 3s1 3-1 4M10 3c-1 1 0 2 2 2" stroke="#fff" stroke-width="1.2" fill="none"/></svg>
    </div>
    <ul class="contact-list">
      <li>0031687203316</li>
      <li>Tobias@hartuvo.nl</li>
      <li>www.hartuvo.nl</li>
    </ul>
    <p class="slogan">BECAUSE QUALITY MATTERS</p>
  </section>

  <section class="card card--back" aria-label="Card back">
    <div class="back-square" aria-hidden="true"></div>
    <p class="back-wordmark">hartuvo</p>
    <p class="back-tagline">The highest quality<br>OEM parts</p>
  </section>
</main>
</body>
</html>
```